Business software developers new website

We need to redesign our website. Our current website is http://www.plovencast.example/index.html, which is outdated and needs a new look. We moved out from web design and have concentrated more on the back end of the systems, for example, system support and security and cloud-based applications. Our major clients include both private and government sectors. We would like to see some designs that are all in one page, simple and clean. Prefer illustrator or obstructed images instead of real-life photos. Must look futuristic yet friendly. Attached the new logo for your references and good luck.

Target Market(s)

Medium to big company for their IT or data management. Either improve or upgrade their current system.

Industry/Entity Type

Business Software

Number of Pages Required

1 page

Colors

Designer to choose colors to be used in the design.

Requirements
Must have
• Simple and clean. Individual assets must be provided in the correct size and format(png or jpeg). Prefer Goggle fonts. Even though the logo color is red, grey and black, still prefer some modern colors that go well with red. When design, must consider the possibility to convert it into responsive.
Nice to have
• White background
Should not have
• real life photos, no slider

```html
<!DOCTYPE html>
<html lang="en">
<head>
<meta charset="utf-8">
<title>plovencast.net — Digital Agency</title>
<link rel="stylesheet" href="https://fonts.googleapis.com/css2?family=Work+Sans:wght@400;500;600;700&display=swap">
<style>
:root{
  --navy:#2e3d8e;
  --red:#ff3b47;
  --ink:#4a5480;
  --blob:#f3f7fd;
  --field:#f4f8fd;
  --white:#ffffff;
  --black:#141414;
}
*{box-sizing:border-box;margin:0;padding:0}
html,body{width:1200px;height:3109px;overflow:hidden}
body{position:relative;background:var(--white);font-family:"Work Sans",sans-serif;color:var(--navy)}
.abs{position:absolute}
.backdrop{position:absolute;left:0;top:0;width:1200px;height:3109px}
.logo{left:231px;top:36px;font-size:23px;font-weight:500;color:#222;letter-spacing:-.3px;display:flex;align-items:center;gap:6px}
.logo .dot{width:9px;height:9px;background:var(--red);border-radius:50%}
.nav{left:413px;top:41px;display:flex;gap:28px;font-size:12px;font-weight:600}
.nav a{color:var(--navy);text-decoration:none}
.btn-contact{left:836px;top:30px;width:125px;height:39px;background:#fff;box-shadow:0 3px 10px rgba(46,61,142,.12);color:var(--red);font-size:12px;font-weight:600;display:flex;align-items:center;justify-content:center;gap:10px}
.hero-title{left:233px;top:226px;font-size:48px;font-weight:600;line-height:61px;letter-spacing:.3px}
.lead{font-size:12px;line-height:19px;color:var(--ink)}
.hero-lead{left:230px;top:362px;width:360px}
.pill{background:var(--red);color:#fff;border-radius:20px;font-weight:600;display:flex;align-items:center;justify-content:center;box-shadow:0 4px 10px rgba(255,59,71,.25)}
.hero-btn{left:235px;top:423px;width:125px;height:34px;font-size:12px}
.hero-link{left:384px;top:433px;font-size:12px;font-weight:600}
.art{border-radius:24px}
.hero-art{left:712px;top:195px;width:250px;height:288px;background:linear-gradient(160deg,#e9eefc 0%,#c9d3f4 55%,#f3d8c7 100%)}
.h2{font-size:31px;font-weight:600;line-height:41px;letter-spacing:.2px}
.need{left:233px;top:736px}
.need-btn{left:234px;top:844px;width:97px;height:26px;font-size:9px}
.card{background:#fff;box-shadow:0 4px 14px rgba(46,61,142,.1)}
.svc{top:710px;height:240px;padding:18px 12px}
.svc h3{font-size:17px;font-weight:600;line-height:25px;margin:30px 4px 0;height:60px}
.svc p{font-size:9px;line-height:15px;color:var(--ink);margin-top:16px}
.eyebrow{font-size:10.5px;font-weight:500;color:var(--red);letter-spacing:.4px}
.about-art{left:92px;top:1082px;width:414px;height:258px;background:linear-gradient(135deg,#c9de52 0%,#3e9a94 45%,#e6ebf2 100%);border-radius:30px}
.about-para{left:605px;top:1230px;width:360px;font-size:12px;line-height:19px;color:var(--ink)}
.arrows{display:flex;gap:14px;align-items:center}
.shot{width:232px;height:176px}
.shot-a{background:linear-gradient(180deg,#dfe3ea 0%,#5c83b0 30%,#e8e8e8 55%)}
.shot-b{background:linear-gradient(180deg,#1e3f7a 0%,#2d6aa8 60%,#7ab2d9 100%)}
.shot-c{background:linear-gradient(180deg,#2a2727 0%,#6a4c3c 35%,#222 60%)}
.see-more{left:0;width:1200px;top:1989px;text-align:center;font-size:11px;font-weight:600;color:var(--red)}
.post{top:2194px;width:232px;height:219px;padding:30px 27px}
.post h4{font-size:11px;font-weight:600}
.post .date{font-size:9px;margin-top:10px;color:var(--ink)}
.post p{font-size:11.5px;line-height:19px;margin-top:22px;color:var(--ink)}
.post .go{position:absolute;right:27px;bottom:26px}
.post.featured{background:var(--red);box-shadow:none}
.post.featured h4,.post.featured .date,.post.featured p{color:#fff}
.field{background:var(--field);font-size:11px;font-weight:600;padding:0 13px;display:flex;align-items:center}
.send{left:535px;top:2782px;width:124px;height:34px;font-size:12px}
.footer{left:0;top:2859px;width:1200px;height:250px;background:var(--black);color:#fff}
.foot-nav{position:absolute;left:0;width:1200px;top:117px;display:flex;justify-content:center;gap:28px;font-size:11px;font-weight:600}
.copy{position:absolute;left:0;width:1200px;top:162px;text-align:center;font-size:8.5px}
.social{position:absolute;left:0;width:1200px;top:196px;display:flex;justify-content:center;gap:50px}
.social span{width:20px;height:20px;border-radius:50%;background:#fff}
</style>
</head>
<body>
<svg class="backdrop" viewBox="0 0 1200 3109" aria-hidden="true">
  <path fill="#f3f7fd" d="M700 0 H1200 V560 C1150 600 1100 640 1040 620 C960 590 900 560 830 600 C760 640 690 600 650 540 C610 480 640 430 620 380 C600 320 630 260 660 200 C690 140 660 60 700 0Z"/>
  <path fill="#f3f7fd" d="M0 680 C60 670 110 720 100 790 C90 860 150 900 240 940 C360 990 520 960 640 990 C760 1020 860 1000 960 980 C1040 960 1070 900 1100 860 C1140 800 1180 780 1200 770 V1300 C1100 1270 1010 1220 990 1150 C980 1080 1040 1020 1000 1010 C900 990 700 1050 600 1070 C500 1080 420 1060 330 1070 C200 1090 90 1210 0 1280Z"/>
  <path fill="#f3f7fd" d="M0 1590 C60 1560 120 1520 200 1540 C300 1570 400 1600 560 1580 C700 1560 820 1530 960 1560 C1060 1580 1140 1560 1200 1520 V2360 C1140 2400 1050 2450 960 2440 C850 2430 760 2470 680 2510 C600 2550 560 2470 480 2440 C400 2410 300 2150 230 2110 C160 2070 80 2100 0 2090Z"/>
</svg>

<div class="abs logo"><span>plovencast.net</span><span class="dot"></span></div>
<nav class="abs nav"><a href="#">Home.</a><a href="#">About us.</a><a href="#">Portfolio.</a><a href="#">Blog.</a><a href="#">Contact us.</a><a href="#">EN ▾</a></nav>
<div class="abs btn-contact">Contact Us
  <svg width="20" height="10" viewBox="0 0 20 10"><path d="M0 5H18M14 1l4 4-4 4" fill="none" stroke="#ff3b47" stroke-width="1.3"/></svg></div>

<h1 class="abs hero-title">The Spirit of<br>Digital Agency.</h1>
<p class="abs lead hero-lead">Vestibulum ac diam sit amet quam vehicula elementum amet est on dui. Nulla porttitor accumsan tincidunt.</p>
<div class="abs pill hero-btn">More About us</div>
<div class="abs hero-link">Get in Touch.</div>
<div class="abs art hero-art" role="img" aria-label="Isometric illustration of a person working at a desk with a computer"></div>

<h2 class="abs h2 need">Anything<br>you need</h2>
<div class="abs pill need-btn">Get in Touch</div>

<div class="abs card svc" style="left:418px;width:169px">
  <svg width="38" height="38" viewBox="0 0 38 38"><rect x="2" y="3" width="34" height="32" fill="none" stroke="#2e3d8e" stroke-width="1.5"/><path d="M2 3l17 14 17-14" fill="none" stroke="#2e3d8e" stroke-width="1.5"/><circle cx="19" cy="11" r="4" fill="none" stroke="#ff3b47" stroke-width="1.5"/></svg>
  <h3>Web &amp; Graphic Design</h3>
  <p>Vestibulum ac diam sit amet quam vehicula elementum amet est on dui. Nulla porttitor ac-cumsan tincidunt.</p>
</div>
<div class="abs card svc" style="left:606px;width:168px">
  <svg width="42" height="30" viewBox="0 0 42 30"><rect x="1" y="1" width="40" height="28" fill="none" stroke="#2e3d8e" stroke-width="1.5"/><path d="M1 6H41" stroke="#2e3d8e" stroke-width="1.5"/><path d="M17 13l-4 4 4 4M25 13l4 4-4 4M22 12l-2 10" fill="none" stroke="#ff3b47" stroke-width="1.4"/></svg>
  <h3>Web &amp; App Development</h3>
  <p>Vestibulum ac diam sit amet quam vehicula elementum amet est on dui. Nulla porttitor ac-cumsan tincidunt.</p>
</div>
<div class="abs card svc" style="left:793px;width:169px">
  <svg width="28" height="32" viewBox="0 0 28 32"><path d="M14 1L2 5v10c0 8 6 13 12 16 6-3 12-8 12-16V5z" fill="none" stroke="#2e3d8e" stroke-width="1.5"/><circle cx="14" cy="14" r="5" fill="none" stroke="#ff3b47" stroke-width="1.4"/></svg>
  <h3>System Suppport &amp; Security</h3>
  <p>Vestibulum ac diam sit amet quam vehicula elementum amet est on dui. Nulla porttitor ac-cumsan tincidunt.</p>
</div>

<div class="abs art about-art" role="img" aria-label="Illustration of a laptop with a cloud on screen, chat bubbles, a gear and a globe"></div>
<div class="abs eyebrow" style="left:607px;top:1095px">OUR COMPANY</div>
<h2 class="abs h2" style="left:605px;top:1122px">Some Fine<br>Words About Us</h2>
<p class="abs about-para">Vestibulum ac diam sit amet quam vehicula elementum amet est on dui. Nulla porttitor accumsan tincidunt.Vestibulum ac diam sit amet.<br>Quam vehicula elementum amet est on dui. Nulla porttitor ac-cumsan tincidunt.</p>
<div class="abs arrows" style="left:605px;top:1352px">
  <svg width="12" height="10" viewBox="0 0 12 10"><path d="M12 5H1M5 1L1 5l4 4" fill="none" stroke="#9aa3c4" stroke-width="1.2"/></svg>
  <svg width="20" height="10" viewBox="0 0 20 10"><path d="M0 5H18M14 1l4 4-4 4" fill="none" stroke="#2e3d8e" stroke-width="1.5"/></svg>
</div>

<h2 class="abs h2" style="left:233px;top:1462px">See some of our<br>Creative work.</h2>
<div class="abs arrows" style="left:918px;top:1521px">
  <svg width="12" height="10" viewBox="0 0 12 10"><path d="M12 5H1M5 1L1 5l4 4" fill="none" stroke="#9aa3c4" stroke-width="1.2"/></svg>
  <svg width="20" height="10" viewBox="0 0 20 10"><path d="M0 5H18M14 1l4 4-4 4" fill="none" stroke="#2e3d8e" stroke-width="1.5"/></svg>
</div>
<div class="abs shot shot-a" style="left:231px;top:1586px" role="img" aria-label="Website screenshot with a city skyline banner"></div>
<div class="abs shot shot-b" style="left:480px;top:1586px" role="img" aria-label="Website screenshot with a starry blue sky and a form"></div>
<div class="abs shot shot-c" style="left:730px;top:1586px" role="img" aria-label="Restaurant website screenshot with dark theme"></div>
<div class="abs shot shot-a" style="left:231px;top:1783px" role="img" aria-label="Website screenshot with a city skyline banner"></div>
<div class="abs shot shot-b" style="left:480px;top:1783px" role="img" aria-label="Website screenshot with a starry blue sky and a form"></div>
<div class="abs shot shot-c" style="left:730px;top:1783px" role="img" aria-label="Restaurant website screenshot with dark theme"></div>
<div class="abs see-more">See More of These.</div>

<div class="abs eyebrow" style="left:239px;top:2094px">BLOG STORIES</div>
<h2 class="abs h2" style="left:234px;top:2115px">Check Our News</h2>
<div class="abs arrows" style="left:918px;top:2135px">
  <svg width="12" height="10" viewBox="0 0 12 10"><path d="M12 5H1M5 1L1 5l4 4" fill="none" stroke="#9aa3c4" stroke-width="1.2"/></svg>
  <svg width="20" height="10" viewBox="0 0 20 10"><path d="M0 5H18M14 1l4 4-4 4" fill="none" stroke="#2e3d8e" stroke-width="1.5"/></svg>
</div>
<article class="abs card post featured" style="left:232px">
  <h4>New Adventure</h4><div class="date">17 May 2019</div>
  <p>Vestibulum ac diam sit amet quam vehicula elementum amet est on dui. Nulla porttitor ac-cumsan tincidunt.</p>
  <svg class="go" width="20" height="10" viewBox="0 0 20 10"><path d="M0 5H18M14 1l4 4-4 4" fill="none" stroke="#fff" stroke-width="1.3"/></svg>
</article>
<article class="abs card post" style="left:482px">
  <h4>New Adventure</h4><div class="date">17 May 2019</div>
  <p>Vestibulum ac diam sit amet quam vehicula elementum amet est on dui. Nulla porttitor ac-cumsan tincidunt.</p>
  <svg class="go" width="20" height="10" viewBox="0 0 20 10"><path d="M0 5H18M14 1l4 4-4 4" fill="none" stroke="#ff3b47" stroke-width="1.3"/></svg>
</article>
<article class="abs card post" style="left:732px">
  <h4>New Adventure</h4><div class="date">17 May 2019</div>
  <p>Vestibulum ac diam sit amet quam vehicula elementum amet est on dui. Nulla porttitor ac-cumsan tincidunt.</p>
  <svg class="go" width="20" height="10" viewBox="0 0 20 10"><path d="M0 5H18M14 1l4 4-4 4" fill="none" stroke="#ff3b47" stroke-width="1.3"/></svg>
</article>

<div class="abs eyebrow" style="left:234px;top:2520px">CONTACT US</div>
<h2 class="abs h2" style="left:234px;top:2540px">Get in Touch</h2>
<div class="abs field" style="left:231px;top:2605px;width:357px;height:38px">Your email</div>
<div class="abs field" style="left:607px;top:2605px;width:356px;height:38px">Subject</div>
<div class="abs field" style="left:233px;top:2668px;width:730px;height:72px;align-items:flex-start;padding-top:18px">Message here...</div>
<div class="abs pill send">Send Message</div>

<footer class="abs footer">
  <nav class="foot-nav"><span>Home.</span><span>About us.</span><span>Portfolio.</span><span>Blog.</span><span>Contact us.</span></nav>
  <div class="copy">© 2019 - plovencast, All Right Reserved</div>
  <div class="social"><span aria-label="Social profile one"></span><span aria-label="Social profile two"></span><span aria-label="Social profile three"></span></div>
</footer>
</body>
</html>
```